Design an infographic - a business case for a water sensitive city

Our company is a research organisation - see www.brightmeadowhubs.org.au. Our work is focused on the re-design of cities to make them more sustainable and liveable, with water as the catalyst.

One of the keys to successful implementation of our research ideas is the 'business case' that demonstrates to decision makers that the benefits of this approach to water management outweigh the costs (it usually costs extra!).

We have realised that traditional business case approaches wont cut it because they focus on the cheapest option, not the one that best satisfies community needs. So a new approach is needed. This is the focus of the infographic. It will highlight the crucial questions to ask (and answer obviously!) in a business case and importantly will highlight a few of the benefits. Statistics emerging from our research have been included to back this up.

The infographic will be used as a marketing and stakeholder engagement piece, so will be included in presentations, annual reports as well as posters.

The web site gives a feel for the corporate colour scheme however style is open to new ideas.

The attached powerpoint file shows five separate but linked concepts that should be included in the infographic. 1. the drivers/need 2. key questions you need to ask when developing your business case 3 . where/how the answers to these questions fit back into a traditional business case process 4. an overview of the benefits of creating a water sensitive city 5. stats. to show that these benefits are real.

These slides have the content but need a design that is consistent across the ideas and ties them together to make a cohesive infographic.

Industry/Entity Type

Marketing

Colors
0555a3
85abd2
f78f20
faa54b

```html
<!DOCTYPE html>
<html lang="en">
<head>
<meta charset="utf-8">
<title>Building a Business Case for a Water Sensitive City</title>
<link rel="stylesheet" href="https://fonts.googleapis.com/css2?family=Oswald:wght@400;500;600;700&family=Varela+Round&family=Roboto+Condensed:wght@400;700&display=swap">
<style>
  :root {
    --blue: #0555a3;
    --blue-light: #85abd2;
    --orange: #f78f20;
    --orange-light: #faa54b;
    --grey: #c9c9c9;
    --grey-dark: #555;
    --green: #3db23a;
    --ink: #111;
    --white: #fff;
  }
  html, body { margin: 0; padding: 0; overflow: hidden; }
  body { width: 850px; height: 1200px; }
  .canvas {
    position: relative; width: 850px; height: 1200px; overflow: hidden;
    background: linear-gradient(135deg, #3f7fc0 0%, #6d9bcf 50%, #3f7fc0 100%);
  }
  .title-bar {
    position: absolute; left: 24px; top: 26px; width: 802px; height: 49px; margin: 0;
    background: var(--white); border-radius: 12px;
    display: flex; align-items: center; justify-content: center;
    font-family: "Oswald", sans-serif; font-weight: 600; font-size: 31px;
    letter-spacing: 0.5px; color: var(--blue); text-transform: uppercase;
  }
  .panel { position: absolute; background: var(--white); border-radius: 16px; overflow: hidden; }
  .panel svg { display: block; width: 100%; height: 100%; }
  .panel-drivers { left: 26px; top: 96px; width: 800px; height: 223px; }
  .panel-questions { left: 26px; top: 337px; width: 395px; height: 446px; }
  .panel-process { left: 436px; top: 337px; width: 390px; height: 446px; }
  .panel-benefits { left: 26px; top: 800px; width: 395px; height: 376px; }
  .panel-examples { left: 436px; top: 800px; width: 390px; height: 376px; }

  .heading { font-family: "Varela Round", sans-serif; font-size: 14px; fill: var(--blue); }
  .cond { font-family: "Oswald", sans-serif; }
  .body { font-family: "Roboto Condensed", sans-serif; font-size: 8px; fill: var(--ink); }
  .blue { fill: var(--blue); }
  .orange { fill: var(--orange); }
  .white { fill: var(--white); }
  .ink { fill: var(--ink); }
  .drop { fill: var(--orange); }
  .drop-num { font-family: "Oswald", sans-serif; font-size: 9px; fill: var(--white); font-weight: 600; }
  .art { fill: url(#artTone); }
  .q-box { fill: none; stroke: var(--blue); stroke-width: 3; }
  .q-title { font-family: "Oswald", sans-serif; font-weight: 500; fill: var(--blue); }
  .q-item { font-family: "Roboto Condensed", sans-serif; font-size: 9px; fill: var(--ink); }
  .badge { fill: var(--orange); }
  .badge-text { font-family: "Oswald", sans-serif; font-weight: 600; font-size: 8.5px; fill: var(--white); }
  .flow-line { stroke: var(--orange); stroke-width: 3; fill: none; }
  .step { fill: #dadada; }
  .step-text { font-family: "Oswald", sans-serif; font-size: 5.6px; font-weight: 600; fill: var(--grey-dark); }
  .feed { stroke: #888; stroke-width: 0.8; fill: none; }
  .feed-text { font-family: "Roboto Condensed", sans-serif; font-size: 4.6px; fill: #444; }
  .num-dot { fill: var(--blue); }
</style>
</head>
<body>
<main class="canvas" role="img" aria-label="Background of diagonal blue and white stripes">
  <h1 class="title-bar">Building a Business Case for a Water Sensitive City</h1>

  <!-- Section 1: drivers -->
  <section class="panel panel-drivers">
    <svg viewBox="0 0 664 185">
      <defs>
        <linearGradient id="artTone" x1="0" y1="0" x2="1" y2="1">
          <stop offset="0" stop-color="#dfe9f4"/><stop offset="1" stop-color="#c4d6ea"/>
        </linearGradient>
        <symbol id="house" viewBox="0 0 34 30"><path d="M17 0 L34 14 L30 14 L30 30 L4 30 L4 14 L0 14 Z"/></symbol>
      </defs>
      <path class="drop" d="M16 10 C16 10 8 20 8 25 a8 8 0 0 0 16 0 C24 20 16 10 16 10Z"/>
      <text class="drop-num" x="16" y="28.5" text-anchor="middle">1.</text>
      <text class="heading" x="36" y="20" textLength="238" lengthAdjust="spacingAndGlyphs">Communities are calling out for</text>
      <text class="heading" x="36" y="36" textLength="230" lengthAdjust="spacingAndGlyphs">new water services in our cities</text>

      <g class="households">
        <use href="#house" x="13" y="44" width="34" height="30" fill="#f78f20"/>
        <use href="#house" x="52" y="44" width="34" height="30" fill="#f78f20"/>
        <use href="#house" x="91" y="44" width="34" height="30" fill="#f78f20"/>
        <use href="#house" x="130" y="44" width="34" height="30" fill="#f78f20"/>
        <use href="#house" x="169" y="44" width="34" height="30" fill="#f78f20"/>
        <use href="#house" x="13" y="88" width="34" height="30" fill="#f78f20"/>
        <use href="#house" x="52" y="88" width="34" height="30" fill="#c9c9c9"/>
        <use href="#house" x="91" y="88" width="34" height="30" fill="#c9c9c9"/>
        <use href="#house" x="130" y="88" width="34" height="30" fill="#c9c9c9"/>
        <use href="#house" x="169" y="88" width="34" height="30" fill="#c9c9c9"/>
      </g>
      <text class="cond ink" x="13" y="152" font-size="26" font-weight="700" textLength="190" lengthAdjust="spacingAndGlyphs"><tspan class="orange">6</tspan> IN <tspan class="orange">10</tspan> HOUSEHOLDS</text>
      <text class="cond ink" x="13" y="170" font-size="8" font-weight="600" textLength="190" lengthAdjust="spacingAndGlyphs">CONSIDER THEMSELVES <tspan class="orange">ENVIRONMENTALLY SUSTAINABLE</tspan></text>

      <rect class="art" x="318" y="6" width="100" height="100" rx="4" role="img" aria-label="Roof gutter feeding a small rain garden planter with flowers"/>
      <text class="cond ink" font-size="10" font-weight="600" transform="translate(252 130) rotate(-90)" textLength="76" lengthAdjust="spacingAndGlyphs">MORE THAN</text>
      <text class="cond blue" x="258" y="130" font-size="96" font-weight="700" textLength="100" lengthAdjust="spacingAndGlyphs">50%</text>
      <text class="cond ink" x="238" y="143" font-size="18" font-weight="700" textLength="170" lengthAdjust="spacingAndGlyphs">OF PEOPLE <tspan class="blue">SUPPORT</tspan></text>
      <text class="cond ink" x="238" y="160" font-size="14" font-weight="700" textLength="170" lengthAdjust="spacingAndGlyphs">THE INSTALLATION OF RAIN</text>
      <text class="cond ink" x="238" y="176" font-size="14" font-weight="700" textLength="170" lengthAdjust="spacingAndGlyphs">GARDENS IN THEIR STREET</text>

      <text class="cond blue" x="440" y="40" font-size="38" font-weight="700" textLength="58" lengthAdjust="spacingAndGlyphs">80%</text>
      <text class="cond ink" x="503" y="20" font-size="9" font-weight="600" textLength="150" lengthAdjust="spacingAndGlyphs">OF HOUSEHOLDERS SAY THEY ARE WILLING</text>
      <text class="cond ink" x="503" y="34" font-size="11" font-weight="600" textLength="150" lengthAdjust="spacingAndGlyphs">TO USE <tspan class="orange">RECYCLED WATER</tspan> FOR</text>
      <text class="cond ink" x="503" y="47" font-size="8" font-weight="600" textLength="150" lengthAdjust="spacingAndGlyphs">NON-DRINKING PURPOSES IN THE HOME</text>
      <rect class="art" x="443" y="56" width="212" height="30" rx="3" role="img" aria-label="Row of ten figures, eight in orange and two in grey"/>
      <g stroke="#111" stroke-width="1.5" fill="none">
        <path d="M545 90 V99 M470 99 H620 M470 99 V112 M545 99 V112 M620 99 V112"/>
      </g>
      <rect class="art" x="440" y="112" width="60" height="63" role="img" aria-label="Toilet icon"/>
      <rect class="art" x="515" y="112" width="60" height="63" role="img" aria-label="Washing machine icon"/>
      <rect class="art" x="590" y="112" width="60" height="63" role="img" aria-label="Watering can icon"/>
    </svg>
  </section>

  <!-- Section 2: questions -->
  <section class="panel panel-questions">
    <svg viewBox="0 0 328 370">
      <defs>
        <marker id="arrowBlue" viewBox="0 0 10 10" refX="8" refY="5" markerWidth="5" markerHeight="5" orient="auto-start-reverse"><path d="M0 0 L10 5 L0 10Z" fill="#0555a3"/></marker>
      </defs>
      <path class="drop" d="M16 8 C16 8 8 18 8 23 a8 8 0 0 0 16 0 C24 18 16 8 16 8Z"/>
      <text class="drop-num" x="16" y="26.5" text-anchor="middle">2.</text>
      <text class="heading" x="36" y="22" textLength="186" lengthAdjust="spacingAndGlyphs">There are 5 questions to ask</text>

      <text class="cond blue" x="38" y="78" font-size="34" font-weight="600" text-anchor="middle">$</text>
      <text class="cond blue" x="290" y="78" font-size="34" font-weight="600" text-anchor="middle">$</text>
      <rect class="q-box" x="63" y="36" width="192" height="56" rx="12"/>
      <text class="q-title" x="159" y="60" font-size="15" text-anchor="middle" textLength="150" lengthAdjust="spacingAndGlyphs">WHICH OPTION HAS THE</text>
      <text class="q-title" x="159" y="79" font-size="15" text-anchor="middle" textLength="172" lengthAdjust="spacingAndGlyphs">LOWEST COMMUNITY COST?</text>

      <g stroke="#0555a3" stroke-width="2" fill="none">
        <path d="M86 92 V126" marker-end="url(#arrowBlue)"/>
        <path d="M232 92 V126" marker-end="url(#arrowBlue)"/>
        <path d="M160 158 H183" marker-start="url(#arrowBlue)" marker-end="url(#arrowBlue)"/>
        <path d="M86 217 V231" marker-start="url(#arrowBlue)" marker-end="url(#arrowBlue)"/>
        <path d="M250 217 V231" marker-start="url(#arrowBlue)" marker-end="url(#arrowBlue)"/>
        <path d="M160 300 H183" marker-end="url(#arrowBlue)"/>
      </g>

      <rect class="q-box" x="15" y="130" width="143" height="85" rx="12"/>
      <text class="q-title" x="86" y="152" font-size="17" text-anchor="middle" textLength="108" lengthAdjust="spacingAndGlyphs">WHO BENEFITS?</text>
      <text class="q-item" x="86" y="166" text-anchor="middle">Utilities</text>
      <text class="q-item" x="86" y="177" text-anchor="middle">Councils</text>
      <text class="q-item" x="86" y="188" text-anchor="middle">Home owners</text>
      <text class="q-item" x="86" y="199" text-anchor="middle">Developers</text>

      <rect class="q-box" x="185" y="130" width="130" height="85" rx="12"/>
      <text class="q-title" x="250" y="152" font-size="17" text-anchor="middle" textLength="104" lengthAdjust="spacingAndGlyphs">WHO WILL PAY?</text>
      <text class="q-item" x="250" y="165" text-anchor="middle">Local communities</text>
      <text class="q-item" x="250" y="175" text-anchor="middle">Home owners</text>
      <text class="q-item" x="250" y="185" text-anchor="middle">Utilities and councils</text>
      <text class="q-item" x="250" y="195" text-anchor="middle">Developers</text>
      <text class="q-item" x="250" y="205" text-anchor="middle">Governments</text>

      <rect class="q-box" x="15" y="235" width="143" height="122" rx="12"/>
      <text class="q-title" x="86" y="252" font-size="9.5" text-anchor="middle" textLength="118" lengthAdjust="spacingAndGlyphs">WHAT ARE THE CHANGES TO THE</text>
      <text class="q-title" x="86" y="270" font-size="17" text-anchor="middle" textLength="100" lengthAdjust="spacingAndGlyphs">WATER CYCLE?</text>
      <text class="q-item" x="86" y="284" text-anchor="middle">Green infrastructure</text>
      <text class="q-item" x="86" y="294" text-anchor="middle">Water conservation</text>
      <text class="q-item" x="86" y="304" text-anchor="middle">Reduced runoff</text>
      <text class="q-item" x="86" y="314" text-anchor="middle">Water supplies</text>
      <text class="q-item" x="86" y="324" text-anchor="middle">Urban cooling</text>
      <text class="q-item" x="86" y="334" text-anchor="middle">Resources &amp; energy</text>
      <text class="q-item" x="86" y="344" text-anchor="middle">Flood protection</text>

      <rect class="q-box" x="185" y="235" width="130" height="122" rx="12"/>
      <text class="q-title" x="250" y="252" font-size="9.5" text-anchor="middle" textLength="110" lengthAdjust="spacingAndGlyphs">WHAT DOES IT MEAN FOR THE</text>
      <text class="q-title" x="250" y="270" font-size="17" text-anchor="middle" textLength="90" lengthAdjust="spacingAndGlyphs">COMMUNITY?</text>
      <text class="q-item" x="250" y="284" text-anchor="middle">Safety</text>
      <text class="q-item" x="250" y="294" text-anchor="middle">Cleaner rivers</text>
      <text class="q-item" x="250" y="304" text-anchor="middle">Better health</text>
      <text class="q-item" x="250" y="314" text-anchor="middle">Sustainability</text>
      <text class="q-item" x="250" y="324" text-anchor="middle">Ecosystem services</text>
      <text class="q-item" x="250" y="334" text-anchor="middle">Developer returns</text>
      <text class="q-item" x="250" y="344" text-anchor="middle">Savings (water, cost)</text>

      <circle class="badge" cx="156" cy="112" r="20"/>
      <text class="badge-text" x="156" y="110" text-anchor="middle" textLength="30" lengthAdjust="spacingAndGlyphs">THE LIFE</text>
      <text class="badge-text" x="156" y="120" text-anchor="middle" textLength="28" lengthAdjust="spacingAndGlyphs">CYCLES</text>

      <circle class="badge" cx="156" cy="225" r="20"/>
      <text class="badge-text" x="156" y="223" text-anchor="middle">THE</text>
      <text class="badge-text" x="156" y="233" text-anchor="middle" textLength="32" lengthAdjust="spacingAndGlyphs">BENEFITS</text>
    </svg>
  </section>

  <!-- Section 3: business case process -->
  <section class="panel panel-process">
    <svg viewBox="0 0 324 370">
      <defs>
        <marker id="arrowGrey" viewBox="0 0 10 10" refX="8" refY="5" markerWidth="4" markerHeight="4" orient="auto"><path d="M0 0 L10 5 L0 10Z" fill="#888"/></marker>
      </defs>
      <path class="drop" d="M16 8 C16 8 8 18 8 23 a8 8 0 0 0 16 0 C24 18 16 8 16 8Z"/>
      <text class="drop-num" x="16" y="26.5" text-anchor="middle">3.</text>
      <text class="heading" x="36" y="22" textLength="96" lengthAdjust="spacingAndGlyphs">Business Cases</text>
      <g class="body" font-size="6.3">
        <text x="191" y="10">Population growth</text>
        <text x="191" y="18">Aging infrastructure</text>
        <text x="191" y="26">Reduced liveability</text>
        <text x="191" y="34">Affordability</text>
        <text x="266" y="10">Droughts</text>
        <text x="266" y="18">Flooding</text>
        <text x="266" y="26">Heat waves</text>
        <text x="266" y="34">Densification</text>
      </g>

      <g stroke="#888" stroke-width="1" fill="none">
        <path d="M94 55 H20 V63"/>
        <path d="M20 76 V171"/>
        <path d="M20 184 V246 H42"/>
        <path d="M73 76 V95"/>
        <path d="M73 108 V127"/>
        <path d="M73 140 V209"/>
        <path d="M73 222 V240"/>
        <path d="M73 253 V272 M35 272 H97 M35 272 V282 M97 272 V282"/>
        <path d="M35 295 V308 M97 295 V308 M35 308 H97 M73 308 V318"/>
        <path d="M73 331 V347"/>
        <path d="M110 354 H121"/>
      </g>

      <g class="feed">
        <path d="M232 72 H80" marker-end="url(#arrowGrey)"/>
        <path d="M136 106 H104" marker-end="url(#arrowGrey)"/>
        <path d="M116 144 V134 H104" marker-end="url(#arrowGrey)"/>
        <path d="M268 188 H76 V208" marker-end="url(#arrowGrey)"/>
        <path d="M198 247 H110" marker-end="url(#arrowGrey)"/>
        <path d="M232 325 H108" marker-end="url(#arrowGrey)"/>
      </g>
      <g class="feed-text">
        <text x="190" y="70">Feeds into</text>
        <text x="108" y="104">Feeds into</text>
        <text x="118" y="131">Feeds into</text>
        <text x="200" y="186">Feeds into</text>
        <text x="140" y="245">Feeds into</text>
        <text x="160" y="323">Feeds into</text>
      </g>

      <g class="flow-line">
        <path d="M138 55 H200 L232 62"/>
        <path d="M238 82 L178 104"/>
        <path d="M140 125 L128 146"/>
        <path d="M274 90 L286 168"/>
        <path d="M276 206 L242 234"/>
        <path d="M230 276 L250 306"/>
      </g>

      <text class="cond ink" x="64" y="43" font-size="7.5" font-weight="600">NO</text>
      <text class="cond ink" x="160" y="43" font-size="7.5" font-weight="600">YES</text>

      <g class="steps">
        <rect class="step" x="8" y="63" width="72" height="13"/><text class="step-text" x="44" y="72" text-anchor="middle">DEFINE THE PROBLEM</text>
        <rect class="step" x="44" y="95" width="58" height="13"/><text class="step-text" x="73" y="104" text-anchor="middle">SET OBJECTIVES</text>
        <rect class="step" x="44" y="127" width="58" height="13"/><text class="step-text" x="73" y="136" text-anchor="middle">DEFINE CRITERIA</text>
        <rect class="step" x="6" y="171" width="58" height="13"/><text class="step-text" x="35" y="180" text-anchor="middle">DEFINE AS 'USUAL'</text>
        <rect class="step" x="42" y="209" width="64" height="13"/><text class="step-text" x="74" y="218" text-anchor="middle">IDENTIFY OPTIONS</text>
        <rect class="step" x="42" y="240" width="66" height="13"/><text class="step-text" x="75" y="249" text-anchor="middle">EVALUATE OPTIONS</text>
        <rect class="step" x="8" y="282" width="54" height="13"/><text class="step-text" x="35" y="291" text-anchor="middle">FINANCIAL</text>
        <rect class="step" x="70" y="282" width="54" height="13"/><text class="step-text" x="97" y="291" text-anchor="middle">INTANGIBLE</text>
        <rect class="step" x="42" y="318" width="64" height="13"/><text class="step-text" x="74" y="327" text-anchor="middle">DECISION MAKING</text>
        <rect class="step" x="40" y="347" width="70" height="13"/><text class="step-text" x="75" y="356" text-anchor="middle">PREFERRED OPTION</text>
        <rect class="step" x="121" y="347" width="50" height="13"/><text class="step-text" x="146" y="356" text-anchor="middle">FUNDING</text>
      </g>

      <circle class="badge" cx="116" cy="55" r="22"/>
      <g class="badge-text" font-size="5.5" text-anchor="middle">
        <text x="116" y="46" textLength="18" lengthAdjust="spacingAndGlyphs">WATER</text>
        <text x="116" y="53" textLength="34" lengthAdjust="spacingAndGlyphs">SENSITIVE CITY</text>
        <text x="116" y="62" font-size="8" textLength="30" lengthAdjust="spacingAndGlyphs">BUSINESS</text>
        <text x="116" y="70" font-size="7" textLength="18" lengthAdjust="spacingAndGlyphs">CASE?</text>
      </g>
      <circle class="badge" cx="258" cy="66" r="27"/>
      <text class="badge-text" x="258" y="64" font-size="11" text-anchor="middle" textLength="38" lengthAdjust="spacingAndGlyphs">THREATS</text>
      <text class="badge-text" x="258" y="76" font-size="11" text-anchor="middle" textLength="40" lengthAdjust="spacingAndGlyphs">TO CITIES</text>

      <circle class="badge" cx="158" cy="110" r="22"/>
      <g class="badge-text" text-anchor="middle">
        <text x="158" y="103" font-size="5.5" textLength="32" lengthAdjust="spacingAndGlyphs">SUSTAINABLE</text>
        <text x="158" y="113" font-size="9" textLength="34" lengthAdjust="spacingAndGlyphs">LIVEABLE</text>
        <text x="158" y="121" font-size="6" textLength="26" lengthAdjust="spacingAndGlyphs">RESILIENT</text>
      </g>
      <text class="body" x="186" y="104" font-size="6.3">A vision for a</text>
      <text class="body" x="186" y="112" font-size="6.3">water sensitive city</text>

      <circle class="badge" cx="116" cy="164" r="20"/>
      <text class="badge-text" x="116" y="167" font-size="8" text-anchor="middle" textLength="30" lengthAdjust="spacingAndGlyphs">BENEFITS</text>

      <circle class="badge" cx="290" cy="190" r="23"/>
      <text class="badge-text" x="290" y="188" font-size="8.5" text-anchor="middle" textLength="28" lengthAdjust="spacingAndGlyphs">ENGAGE</text>
      <text class="badge-text" x="290" y="197" font-size="5.5" text-anchor="middle" textLength="36" lengthAdjust="spacingAndGlyphs">BENEFICIARIES</text>

      <circle class="badge" cx="222" cy="253" r="25"/>
      <text class="badge-text" x="222" y="251" font-size="8" text-anchor="middle" textLength="34" lengthAdjust="spacingAndGlyphs">LIFECYCLE</text>
      <text class="badge-text" x="222" y="263" font-size="11" text-anchor="middle" textLength="28" lengthAdjust="spacingAndGlyphs">COSTS</text>

      <circle class="badge" cx="256" cy="330" r="25"/>
      <text class="badge-text" x="256" y="328" font-size="8" text-anchor="middle" textLength="38" lengthAdjust="spacingAndGlyphs">COMMUNITY</text>
      <text class="badge-text" x="256" y="339" font-size="8" text-anchor="middle" textLength="22" lengthAdjust="spacingAndGlyphs">COSTS</text>
    </svg>
  </section>

  <!-- Section 4: benefits -->
  <section class="panel panel-benefits">
    <svg viewBox="0 0 328 312">
      <path class="drop" d="M16 8 C16 8 8 18 8 23 a8 8 0 0 0 16 0 C24 18 16 8 16 8Z"/>
      <text class="drop-num" x="16" y="26.5" text-anchor="middle">4.</text>
      <text class="heading" x="36" y="20" textLength="146" lengthAdjust="spacingAndGlyphs">Benefits of creating</text>
      <text class="heading" x="36" y="37" textLength="154" lengthAdjust="spacingAndGlyphs">a water sensitive city</text>

      <g class="body">
        <circle class="num-dot" cx="17" cy="55" r="5"/><text class="white" x="17" y="58" font-size="7" text-anchor="middle">1</text>
        <text x="25" y="58">Natural systems treat</text>
        <text x="12" y="67">pollutants, create a sense of place</text>
        <text x="12" y="76">and provide ecosystem services</text>

        <circle class="num-dot" cx="17" cy="140" r="5"/><text class="white" x="17" y="143" font-size="7" text-anchor="middle">2</text>
        <text x="25" y="143">Storm water and sewerage is</text>
        <text x="12" y="152">managed as a resource rather than</text>
        <text x="12" y="161">a waste. Flows and pollutants are</text>
        <text x="12" y="170">retained</text>

        <circle class="num-dot" cx="17" cy="183" r="5"/><text class="white" x="17" y="186" font-size="7" text-anchor="middle">3</text>
        <text x="25" y="186">Waste water can provide</text>
        <text x="12" y="195">energy, nutrients and minerals</text>

        <circle class="num-dot" cx="17" cy="256" r="5"/><text class="white" x="17" y="259" font-size="7" text-anchor="middle">4</text>
        <text x="25" y="259">Corridors of green and blue</text>
        <text x="12" y="268">throughout cities create space for</text>
        <text x="12" y="277">flood waters when it rains and</text>
        <text x="12" y="286">space for play at other times</text>

        <circle class="num-dot" cx="195" cy="126" r="5"/><text class="white" x="195" y="129" font-size="7" text-anchor="middle">5</text>
        <text x="203" y="129">Precious drinking water is</text>
        <text x="191" y="138">conserved by water efficiency and</text>
        <text x="191" y="147">using alternative supplies where</text>
        <text x="191" y="156">drinking water isn't required</text>

        <circle class="num-dot" cx="195" cy="273" r="5"/><text class="white" x="195" y="276" font-size="7" text-anchor="middle">6</text>
        <text x="203" y="276">Trees and water in the urban</text>
        <text x="191" y="285">landscape reduce temperatures</text>
        <text x="191" y="294">during heat waves</text>
      </g>

      <rect class="art" x="12" y="82" width="120" height="48" rx="3" role="img" aria-label="Planter bed of green grass with water draining into it"/>
      <rect class="art" x="12" y="203" width="138" height="44" rx="3" role="img" aria-label="Row of houses above green landscape and blue water"/>
      <rect class="art" x="200" y="30" width="112" height="86" rx="3" role="img" aria-label="Blue figure drinking from an orange water fountain"/>
      <rect class="art" x="191" y="166" width="126" height="98" rx="3" role="img" aria-label="Plan of city blocks with green trees and a winding blue waterway"/>
    </svg>
  </section>

  <!-- Section 5: examples -->
  <section class="panel panel-examples">
    <svg viewBox="0 0 324 312">
      <path class="drop" d="M16 8 C16 8 8 18 8 23 a8 8 0 0 0 16 0 C24 18 16 8 16 8Z"/>
      <text class="drop-num" x="16" y="26.5" text-anchor="middle">5.</text>
      <text class="heading" x="36" y="20" textLength="186" lengthAdjust="spacingAndGlyphs">How big are these benefits</text>
      <text class="heading" x="36" y="37" textLength="108" lengthAdjust="spacingAndGlyphs">Some examples</text>

      <rect class="art" x="22" y="44" width="92" height="152" rx="4" role="img" aria-label="Corrugated rainwater tank"/>
      <rect fill="#fff" x="34" y="48" width="70" height="144"/>
      <g class="cond ink" font-weight="700">
        <text x="38" y="76" font-size="30" textLength="60" lengthAdjust="spacingAndGlyphs">SAVE</text>
        <text x="38" y="90" font-size="11" textLength="60" lengthAdjust="spacingAndGlyphs">ON AVERAGE</text>
        <text class="orange" x="38" y="128" font-size="38" textLength="60" lengthAdjust="spacingAndGlyphs">$200</text>
        <text x="38" y="142" font-size="7" textLength="60" lengthAdjust="spacingAndGlyphs">ON YOUR WATER BILL</text>
        <text x="38" y="163" font-size="16" textLength="60" lengthAdjust="spacingAndGlyphs">BY HAVING A</text>
      </g>
      <rect fill="#faa54b" x="36" y="170" width="64" height="14"/>
      <text class="cond ink" x="40" y="181" font-size="9" font-weight="700" textLength="56" lengthAdjust="spacingAndGlyphs">RAINWATER TANK</text>

      <text class="cond ink" x="152" y="67" font-size="16" font-weight="700" textLength="158" lengthAdjust="spacingAndGlyphs">INCREASE PROPERTY VALUE BY</text>
      <rect class="art" x="147" y="80" width="48" height="42" rx="3" role="img" aria-label="Grey house icon"/>
      <text class="cond blue" x="222" y="122" font-size="54" font-weight="700" textLength="88" lengthAdjust="spacingAndGlyphs">3.7%</text>

      <g class="cond orange" font-weight="700" font-size="14">
        <text x="152" y="140" textLength="48" lengthAdjust="spacingAndGlyphs">0.5 - 1°C</text>
        <text x="166" y="172" textLength="34" lengthAdjust="spacingAndGlyphs">1 - 2°C</text>
        <text x="166" y="204" textLength="34" lengthAdjust="spacingAndGlyphs">3 - 5°C</text>
      </g>
      <g class="body" font-size="6.5">
        <text x="214" y="132">Reduction in land surface</text>
        <text x="214" y="140">temperature for every 10%</text>
        <text x="214" y="148">increase in tree cover</text>
        <text x="214" y="166">Temperature reduction will</text>
        <text x="214" y="174">reduce morbidity &amp; mortality</text>
        <text x="214" y="194">Cooling effect of irrigation in</text>
        <text x="214" y="202">Dubbo town centre, compared</text>
        <text x="214" y="210">with unirrigated surrounding</text>
        <text x="214" y="218">rural land, on a 40°C day</text>
      </g>

      <rect class="art" x="22" y="204" width="86" height="30" rx="3" role="img" aria-label="Green city skyline silhouette"/>
      <text class="cond" fill="#3db23a" x="22" y="262" font-size="25" font-weight="700" textLength="107" lengthAdjust="spacingAndGlyphs">GREEN CITY</text>
      <text class="cond ink" x="25" y="292" font-size="21" font-weight="700" textLength="262" lengthAdjust="spacingAndGlyphs">+  <tspan class="blue">WATER</tspan>  =  HEALTH BENEFITS</text>
      <path class="orange" d="M301 280 c-4 -6 -13 -2 -9 5 l9 9 l9 -9 c4 -7 -5 -11 -9 -5z"/>
    </svg>
  </section>
</main>
</body>
</html>
```